Velmora Freightway Solutions Business cards

Would like a very unique design catchy but professional for business cards. Please use log provided.Marlon WellsCeo and Founder TransCon Logistix Solutions1-888-913-3225mwells@tlsolutionsus.comwww.tlsolutionsus.com

```html
<!DOCTYPE html>
<html lang="en">
<head>
<meta charset="utf-8">
<title>Velmora Freightway Solutions – Business Cards</title>
<link href="https://fonts.googleapis.com/css2?family=Open+Sans:wght@400;600;700&display=swap" rel="stylesheet">
<style>
  :root {
    --bg: #1c1c1e;
    --brand-blue: #1273be;
    --navy: #0c2847;
    --accent-red: #d8262f;
    --white: #ffffff;
    --card-w: 560px;
    --card-h: 320px;
  }
  * { box-sizing: border-box; margin: 0; padding: 0; }
  html, body { width: 1200px; height: 960px; overflow: hidden; }
  body {
    background: var(--bg);
    font-family: "Open Sans", Arial, sans-serif;
    position: relative;
  }
  .card {
    position: absolute;
    left: 320px;
    width: var(--card-w);
    height: var(--card-h);
    overflow: hidden;
  }
  /* Back side */
  .card-back { top: 120px; background: var(--brand-blue); }
  .back-wordmark {
    position: absolute; left: 0; right: 0; top: 100px;
    text-align: center; color: var(--white);
    font-weight: 700; font-size: 40px; line-height: 46px; letter-spacing: 1px;
  }
  .back-web {
    position: absolute; left: 0; right: 0; top: 214px;
    text-align: center; color: var(--white);
    font-size: 15px; letter-spacing: 2px; font-weight: 600;
  }
  /* Front side */
  .card-front { top: 520px; background: var(--white); }
  .front-shapes { position: absolute; inset: 0; }
  .brand {
    position: absolute; left: 26px; top: 118px; width: 220px;
    display: flex; align-items: center; gap: 10px;
  }
  .brand-dot { width: 14px; height: 14px; background: var(--accent-red); flex: none; }
  .brand-name {
    color: var(--brand-blue); font-weight: 700; font-size: 17px;
    line-height: 21px; text-transform: uppercase;
  }
  .title-band {
    position: absolute; right: 0; top: 62px; width: 250px; height: 62px;
    background: var(--navy); color: var(--white); text-align: right;
    padding: 10px 22px 0 0;
  }
  .person-name { font-weight: 700; font-size: 19px; line-height: 22px; text-transform: uppercase; }
  .person-role { font-size: 13px; line-height: 20px; text-transform: uppercase; }
  .contact {
    position: absolute; right: 22px; top: 140px;
    color: var(--white); text-align: right; font-size: 14px; line-height: 20px;
    list-style: none;
  }
  .contact .address { margin-bottom: 10px; }
  .contact li { display: flex; justify-content: flex-end; align-items: center; gap: 6px; }
  .contact svg { width: 12px; height: 12px; flex: none; }
</style>
</head>
<body>

<section class="card card-back" aria-label="Back of business card">
  <div class="back-wordmark">VELMORA<br>FREIGHTWAY</div>
  <div class="back-web">www.vfwayroutes.com</div>
</section>

<section class="card card-front" aria-label="Front of business card">
  <svg class="front-shapes" viewBox="0 0 560 320" width="560" height="320" aria-hidden="true">
    <polygon points="190,320 390,0 560,0 560,320" fill="var(--brand-blue)"/>
    <polygon points="300,62 310,62 310,124 270,124" fill="#0f2a1a"/>
  </svg>

  <div class="brand">
    <span class="brand-dot"></span>
    <span class="brand-name">Velmora Freightway Solutions</span>
  </div>

  <div class="title-band">
    <div class="person-name">Dorian Pike</div>
    <div class="person-role">CEO and Founder</div>
  </div>

  <ul class="contact">
    <li class="address">2417 Harlow Creek Rd<br>Marietta, GA 30062</li>
    <li>1-888-470-6158
      <svg viewBox="0 0 12 12"><path d="M3 1l2 2.5-1.2 1.2a6 6 0 0 0 3.5 3.5L8.5 7 11 9l-1.5 2C5 11 1 7 1 2.5z" fill="var(--white)"/></svg>
    </li>
    <li>dpike@vfwayroutes.com
      <svg viewBox="0 0 12 12"><rect x="1" y="2.5" width="10" height="7" rx="1" fill="var(--white)"/><path d="M1.5 3l4.5 3.5L10.5 3" stroke="var(--brand-blue)" fill="none"/></svg>
    </li>
    <li>www.vfwayroutes.com
      <svg viewBox="0 0 12 12"><circle cx="6" cy="6" r="5" fill="none" stroke="var(--white)"/><ellipse cx="6" cy="6" rx="2.2" ry="5" fill="none" stroke="var(--white)"/><path d="M1 6h10" stroke="var(--white)"/></svg>
    </li>
  </ul>
</section>

</body>
</html>
```